Whitcombe Business Card Design

The name of the business is Dario Whitcombe, CPA LLC
The service that we offer is Accounting, Tax & Consulting Services. I need it to have the following items:
Dario Whitcombe, Principal
Phone Number
Email Address
Physical Address

I have attached the company logo, one in black and one in white. Please provide a design in black background and the other in white background. Please include "Accounting, Tax & Consulting Services". I want the business card to be clean and very professional.

```html
<!DOCTYPE html>
<html lang="en">
<head>
<meta charset="UTF-8">
<title>Dario Whitcombe, CPA LLC — Business Card</title>
<link href="https://fonts.googleapis.com/css2?family=Montserrat:wght@500;600;700&family=Mulish:wght@400;500;600&display=swap" rel="stylesheet">
<style>
  :root {
    --backdrop: #2b2b2b;
    --card: #1b1b1b;
    --red: #a8201f;
    --grey: #5b5b5b;
    --grey-light: #7d7d7d;
    --white: #f2f2f2;
  }
  * { box-sizing: border-box; margin: 0; padding: 0; }
  html, body { width: 1200px; height: 900px; overflow: hidden; }
  body {
    background: var(--backdrop);
    display: flex;
    flex-direction: column;
    align-items: center;
    justify-content: center;
    gap: 48px;
    font-family: "Mulish", sans-serif;
  }
  .card {
    position: relative;
    width: 660px;
    height: 377px;
    background: var(--card);
    border-radius: 18px;
    box-shadow: 0 18px 40px rgba(0,0,0,.45);
  }
  .brand {
    display: flex;
    align-items: center;
    gap: 16px;
  }
  .brand-square {
    width: 50px;
    height: 50px;
    border: 5px solid var(--grey);
    flex-shrink: 0;
  }
  .brand-text { display: flex; flex-direction: column; }
  .brand-name {
    font-family: "Montserrat", sans-serif;
    font-weight: 600;
    font-size: 24px;
    letter-spacing: 1px;
    color: var(--grey);
    text-transform: uppercase;
    line-height: 1;
  }
  .brand-title {
    font-family: "Montserrat", sans-serif;
    font-weight: 600;
    font-size: 17px;
    letter-spacing: 2.6px;
    color: var(--grey-light);
    text-transform: uppercase;
    margin-top: 6px;
  }
  .brand-services {
    font-family: "Montserrat", sans-serif;
    font-weight: 700;
    font-size: 14px;
    letter-spacing: .5px;
    color: var(--grey-light);
    margin-top: 12px;
    margin-left: 20px;
  }
  .card-front .brand {
    position: absolute;
    left: 100px;
    top: 130px;
  }
  .card-back .brand {
    position: absolute;
    left: 150px;
    top: 70px;
  }
  .contact {
    position: absolute;
    left: 50px;
    bottom: 64px;
    display: flex;
    align-items: stretch;
    gap: 22px;
  }
  .person-name {
    font-family: "Montserrat", sans-serif;
    font-weight: 700;
    font-size: 15px;
    color: var(--red);
    text-transform: uppercase;
    letter-spacing: .3px;
    margin-bottom: 8px;
  }
  .address { color: var(--white); font-size: 15px; line-height: 1.55; }
  .divider { width: 2px; background: var(--red); }
  .channels { list-style: none; display: flex; flex-direction: column; justify-content: center; gap: 9px; }
  .channels li { display: flex; align-items: center; gap: 12px; color: var(--white); font-size: 15px; white-space: nowrap; }
  .channels svg { width: 16px; height: 16px; fill: var(--red); flex-shrink: 0; }
</style>
</head>
<body>
  <section class="card card-front" aria-label="Card front">
    <div class="brand">
      <span class="brand-square" aria-hidden="true"></span>
      <div class="brand-text">
        <span class="brand-name">Dario Whitcombe, CPA, LLC</span>
        <span class="brand-title">Certified Public Accountant</span>
        <span class="brand-services">Accounting, Tax &amp; Consulting Services</span>
      </div>
    </div>
  </section>

  <section class="card card-back" aria-label="Card back">
    <div class="brand">
      <span class="brand-square" aria-hidden="true"></span>
      <div class="brand-text">
        <span class="brand-name">Dario Whitcombe, CPA, LLC</span>
        <span class="brand-title">Certified Public Accountant</span>
      </div>
    </div>

    <div class="contact">
      <div class="person">
        <p class="person-name">Dario Whitcombe, Principal</p>
        <p class="address">Harborline Plaza 1820 Crest<br>Fenwick Ave NW Suite 710</p>
      </div>
      <span class="divider" aria-hidden="true"></span>
      <ul class="channels">
        <li>
          <svg viewBox="0 0 24 24" aria-hidden="true"><path d="M6.6 10.8a15 15 0 0 0 6.6 6.6l2.2-2.2c.3-.3.7-.4 1-.2 1.1.4 2.3.6 3.6.6.6 0 1 .4 1 1V20c0 .6-.4 1-1 1A17 17 0 0 1 3 4c0-.6.4-1 1-1h3.5c.6 0 1 .4 1 1 0 1.3.2 2.5.6 3.6.1.3 0 .7-.2 1z"/></svg>
          555-204-7391
        </li>
        <li>
          <svg viewBox="0 0 24 24" aria-hidden="true"><path d="M2 5h20v14H2z M3.5 6.5 12 13l8.5-6.5" fill="none" stroke="#a8201f" stroke-width="2"/></svg>
          info@whitcombecpa-example.com
        </li>
        <li>
          <svg viewBox="0 0 24 24" aria-hidden="true"><circle cx="12" cy="12" r="9" fill="none" stroke="#a8201f" stroke-width="2"/><path d="M3 12h18M12 3c3 3 3 15 0 18M12 3c-3 3-3 15 0 18" fill="none" stroke="#a8201f" stroke-width="1.6"/></svg>
          www.whitcombecpa-example.com
        </li>
      </ul>
    </div>
  </section>
</body>
</html>
```